Corvane Grid Works Ltd. -Website Design

We need a site design for a new company based in Toronto, Ontario called 'Corvane Grid Works Ltd.'

We provide Engineering services, Subsurface Utility Engineering services and Geospatial Data Management.

Our clients are typically Utilities (electric, gas, water/waste water, telcom) or contractors/consultants working on their behalf.

Our business model is new and we are the first to offer all three services to our clients; this allows us to provide value-added services from all three of our main offerings.

Target Market(s)

Field Supervisors, Managers, Directors, VP's at Utility companies

Industry/Entity Type

Business

Requirements
Must have
• -The landing page must clearly identify the 3 main business offerings allowing the user to easily navigate to each....Utility Engineering, GIS Data Management & Sub-surface Utility Engineering (SUE).

-Interactive contact page with integrated email

-based on existing logo design...
Nice to have
• -Ability to easily add/post news releases, updates, jobs, etc...

-Ability to integrate instructional YouTube video(s)

Should not have
• -Cannot be too cluttered....

```html
<!DOCTYPE html>
<html lang="en">
<head>
<meta charset="utf-8">
<title>Corvane Grid Works Ltd. – Utility Services</title>
<link rel="stylesheet" href="https://fonts.googleapis.com/css2?family=Arimo:wght@400;700&display=swap">
<style>
  :root {
    --page-bg: #efefef;
    --header-top: #e4e6e6;
    --header-bottom: #ffffff;
    --band-grey: #a8a59e;
    --ink: #111111;
    --heading-blue: #1b4a8c;
    --logo-grey: #4d4d4d;
    --logo-accent: #e2862a;
    --tab-black: #000000;
    --field-border: #7a7a7a;
    --hero-light: #bfe0ee;
    --hero-mid: #8fa3b4;
    --hero-dark: #3a3e4a;
    --plan-light: #d9dde6;
    --plan-mid: #9aa6bf;
    --field-green: #7f9a5c;
    --field-grey: #9c958a;
    --badge-blue: #4b6ea8;
    --badge-grey: #8a8f96;
  }
  * { box-sizing: border-box; margin: 0; padding: 0; }
  html, body { width: 806px; height: 1200px; overflow: hidden; }
  body {
    position: relative;
    background: var(--page-bg);
    font-family: "Arimo", Arial, sans-serif;
    color: var(--ink);
  }
  .site-header {
    position: absolute; left: 0; top: 0; width: 806px; height: 172px;
    background: linear-gradient(var(--header-top), var(--header-bottom) 70%);
  }
  .brand {
    position: absolute; left: 512px; top: 96px;
    display: flex; align-items: center; gap: 10px;
  }
  .brand-mark { width: 30px; height: 30px; background: var(--logo-accent); }
  .brand-name { font-size: 24px; font-weight: 700; color: var(--logo-grey); letter-spacing: 0.5px; }
  .main-nav { position: absolute; left: 25px; top: 134px; display: flex; }
  .main-nav a {
    display: block; height: 38px; line-height: 40px; padding: 0 10px;
    font-size: 24px; color: var(--ink); text-decoration: none; margin-right: 7px;
  }
  .main-nav a.is-current { background: var(--tab-black); color: #fff; border-radius: 6px 6px 0 0; width: 83px; }
  .hero-band { position: absolute; left: 0; top: 172px; width: 806px; height: 280px; background: var(--band-grey); }
  .hero-photo {
    position: absolute; left: 25px; top: 172px; width: 753px; height: 263px;
    border-radius: 0 0 8px 8px; box-shadow: 2px 3px 6px rgba(0,0,0,.45);
    background: linear-gradient(90deg, var(--hero-light), var(--hero-mid) 40%, var(--hero-dark) 70%, var(--hero-light));
  }
  .photo {
    position: absolute; box-shadow: 3px 3px 5px rgba(0,0,0,.5);
  }
  .photo-plans { left: 24px; top: 471px; width: 236px; height: 157px;
    background: linear-gradient(135deg, var(--plan-mid), var(--plan-light)); }
  .photo-field { left: 521px; top: 835px; width: 244px; height: 182px;
    background: linear-gradient(var(--field-green) 45%, var(--field-grey)); }
  .service h2 { font-size: 17px; font-weight: 400; color: var(--heading-blue); margin-bottom: 10px; }
  .service ul { list-style: none; font-size: 12px; line-height: 14.6px; }
  .service { position: absolute; }
  .service-engineering { left: 283px; top: 470px; width: 300px; }
  .service-engineering h2 { margin-bottom: 13px; }
  .service-gis { left: 18px; top: 708px; }
  .service-gis h2 { margin-left: 4px; }
  .service-sue { left: 18px; top: 929px; }
  .contact-form { position: absolute; left: 605px; top: 510px; width: 160px; font-size: 12px; }
  .contact-form label { display: block; margin-bottom: 3px; }
  .contact-form input, .contact-form textarea {
    display: block; width: 160px; height: 20px; border: 1px solid var(--field-border);
    background: #fff; margin-bottom: 17px;
  }
  .contact-form textarea { height: 96px; margin-bottom: 5px; resize: none; }
  .contact-form button {
    display: block; margin-left: 103px; width: 56px; height: 18px;
    font: 700 12px "Arimo", Arial, sans-serif; border: 1px solid #777; border-radius: 3px;
    background: linear-gradient(#fdfdfd, #d8d8d8);
  }
  .site-footer {
    position: absolute; left: 0; top: 1088px; width: 806px; height: 112px;
    background: linear-gradient(#ffffff, var(--page-bg) 40%, #e2e2e2);
  }
  .footer-nav { position: absolute; left: 18px; top: 14px; font-size: 16px; font-weight: 700; }
  .footer-nav a { color: var(--ink); text-decoration: none; }
  .payment-badges { position: absolute; left: 26px; top: 64px; display: flex; gap: 6px; }
  .payment-badges span { width: 32px; height: 20px; background: var(--badge-blue); border-radius: 2px; }
  .payment-badges span:nth-child(2) { background: #f2f2f2; border: 1px solid #ccc; }
  .copyright { position: absolute; left: 244px; top: 79px; font-size: 16px; }
  .social-links { position: absolute; left: 636px; top: 64px; display: flex; gap: 12px; }
  .social-links span { width: 30px; height: 30px; border-radius: 5px; background: var(--badge-grey); }
</style>
</head>
<body>
  <header class="site-header">
    <div class="brand"><span class="brand-mark"></span><span class="brand-name">Corvane Grid Works</span></div>
    <nav class="main-nav">
      <a class="is-current" href="#">Home</a>
      <a href="#">Services</a>
      <a href="#">Contact Us</a>
    </nav>
  </header>

  <div class="hero-band"></div>
  <div class="hero-photo" role="img" aria-label="Team of business professionals in an office"></div>

  <div class="photo photo-plans" role="img" aria-label="Engineers reviewing utility plans"></div>
  <section class="service service-engineering">
    <h2>Utility Engineering Services</h2>
    <ul>
      <li>&gt; Project Management;</li>
      <li>&gt; Outside Plant Network Design;</li>
      <li>&gt; Utility Design and Permitting;</li>
      <li>&gt; Project Management;</li>
      <li>&gt; Surveys and Mapping (GPS);</li>
      <li>&gt; Pole line design and attachment permitting</li>
      <li>&nbsp;&nbsp;&nbsp;(Pole Load Calculations);</li>
      <li>&gt; Specialty Permits for the Utility Industry</li>
      <li>&nbsp;&nbsp;(Railway, Transport Ministry, Conservation Authority);</li>
      <li>&gt; Manhole and Duct Bank Design.</li>
    </ul>
  </section>

  <form class="contact-form">
    <label for="name">Name :</label><input id="name" type="text">
    <label for="phone">Phone :</label><input id="phone" type="text">
    <label for="email">Email :</label><input id="email" type="text">
    <label for="comment">Comment :</label><textarea id="comment"></textarea>
    <button type="button">Submit</button>
  </form>

  <section class="service service-gis">
    <h2>Geographic Information Systems (GIS) Services</h2>
    <ul>
      <li>&gt; GIS Project Management;</li>
      <li>&gt; Records Conversion for GIS Systems;</li>
      <li>&gt; Landbase Data Management;</li>
      <li>&gt; Data Translation and Transformation Between File Formats;</li>
      <li>&gt; Hydro Asset Management using Arcwell;</li>
      <li>&gt; Spatial Data Analysis &amp; Manipulation;</li>
      <li>&gt; Fibre Asset Management using Arcwell &amp; LineTrace Software;</li>
      <li>&gt; Custom Cartographic Mapping;</li>
      <li>&gt; Engineering and Base Mapping using Arcwell, DraftCore, MapLedger;</li>
      <li>&gt; Arcwell Customization &amp; Application Development;</li>
      <li>&gt; Database Development.</li>
    </ul>
  </section>

  <div class="photo photo-field" role="img" aria-label="Field crew surveying a utility manhole beside a trailer"></div>
  <section class="service service-sue">
    <h2>Subsurface Utility Engineering (SUE) Services</h2>
    <ul>
      <li>&gt; Project Management;</li>
      <li>&gt; Consulting;</li>
      <li>&gt; Surveying;</li>
      <li>&gt; CAD Processing of Results.</li>
    </ul>
  </section>

  <footer class="site-footer">
    <nav class="footer-nav"><a href="#">Home</a> | <a href="#">Services</a> | <a href="#">Contact Us</a></nav>
    <div class="payment-badges"><span></span><span></span><span></span><span></span></div>
    <p class="copyright">© 2012 Corvanegrid.ca. All Rights Reserved.</p>
    <div class="social-links"><span></span><span></span><span></span></div>
  </footer>
</body>
</html>
```